Paint Retail Store needs a logo/label redesign.

We are redesigning a label for one of our products. We are a paint retail store that specializes on selling premium paint at outlet prices called Coat & Gleam. We want the redesign to exude professionalism and cleanliness. Attached is a picture of our current label. We want the logo Coat & Gleam to be modified to a more modern feel that still incorporates the iconic paint roller element that has been part of our brand identity. We want the description of: Exceptional Durability/ Luxurious Finish to be included in the front of the label to attract our clients. Include all of the information and description of the current label to the new label. Attached are pictures of our competitors labels so you have an idea of what we are looking for. We also want the background of the label to be a clean solid color.

Target Market(s)

Home Owners, DIY enthusiasts, Contractors/painters, interior designers

Industry/Entity Type

Paint and Coatings retail store

Colors

Designer to choose colors to be used in the design.

Requirements
Must have
• Semigloss Finish, Exceptional Durability, Luxurios Finish. Include all the information that are on the side of the current label to the new label. Include the phrase: Made in the US.
Nice to have
• A redesign of the logo: Coat & Gleam to convey a more modern/professional look.
Should not have
• Feminine colors.

```html
<!DOCTYPE html>
<html lang="en">
<head>
<meta charset="utf-8">
<title>Coat &amp; Gleam Semi-Gloss Latex Paint Label</title>
<link href="https://fonts.googleapis.com/css2?family=Poppins:wght@400;500;600;800&family=Saira+Condensed:wght@400;500&family=Cinzel:wght@500&display=swap" rel="stylesheet">
<style>
  :root{
    --navy-top:#0b1f38;
    --navy-bottom:#1c4280;
    --panel-blue:#0e4a88;
    --orange:#f0821e;
    --white:#ffffff;
    --grey:#a7a9ac;
    --grey-dark:#8a8c8f;
    --gold:#c9a24a;
  }
  *{margin:0;padding:0;box-sizing:border-box}
  html,body{width:1200px;height:870px;overflow:hidden}
  body{background:var(--navy-top);font-family:"Poppins",sans-serif;color:var(--white)}
  .label{position:relative;width:1200px;height:870px;overflow:hidden;
    background:linear-gradient(180deg,var(--navy-top) 0%,#12305a 45%,var(--navy-bottom) 100%)}
  .col{position:absolute;font-size:10.6px;line-height:14.5px;letter-spacing:-.15px}
  .col-left{left:49px;top:62px;width:284px;text-align:justify;font-weight:500;overflow:hidden;height:584px}
  .col-right{left:863px;width:285px;font-weight:400}
  .orange{color:var(--orange)}
  .ingredients{position:absolute;left:62px;top:655px;width:257px;height:174px;background:var(--grey);border-radius:9px;padding:12px 24px;font-size:10.8px;line-height:14.5px}
  .ingredients h3{font-size:16px;font-weight:600;display:flex;gap:20px;border-bottom:2px solid var(--white);padding-bottom:4px;margin-bottom:8px}
  .ing-row{display:flex;justify-content:space-between}
  .ing-row span:first-child{flex:1;overflow:hidden;white-space:nowrap}
  .ing-note{margin-top:18px}
  .finish-tag{position:absolute;left:455px;top:34px;width:290px;height:48px;background:var(--grey);font:800 29px/48px "Poppins",sans-serif;text-align:center;letter-spacing:1px}
  .brand{position:absolute;left:440px;top:170px;width:320px;display:flex;align-items:center;justify-content:center;gap:12px;font:800 44px/1 "Poppins",sans-serif;color:var(--white)}
  .brand-mark{width:26px;height:26px;background:var(--orange)}
  .tagline{position:absolute;left:440px;top:314px;width:320px;text-align:center;font:400 25px/1 "Saira Condensed",sans-serif}
  .grade{position:absolute;left:478px;top:388px;width:242px;text-align:center;font:500 28px/1 "Cinzel",serif;color:var(--gold);border-top:1px solid var(--gold);border-bottom:1px solid var(--gold);padding:4px 0}
  .claim{position:absolute;left:400px;width:400px;text-align:center;font:400 38px/1 "Saira Condensed",sans-serif}
  .claim-1{top:432px}
  .claim-rule{position:absolute;left:530px;top:470px;width:140px;height:3px;background:var(--white)}
  .claim-2{top:476px}
  .art{position:absolute;left:410px;top:535px;width:400px;height:260px;background:linear-gradient(160deg,#b9bbbe,var(--grey-dark));border-radius:6px;opacity:.85}
  .product{position:absolute;left:400px;top:595px;width:400px;text-align:center;font:800 66px/1 "Poppins",sans-serif;color:var(--orange);letter-spacing:-1px}
  .use{position:absolute;left:400px;top:670px;width:400px;text-align:center;font:800 26px/1 "Poppins",sans-serif}
  .seal{position:absolute;left:560px;top:732px;width:80px;height:80px;border-radius:50%;background:#1d8fd8;border:4px solid var(--white)}
  .volume{position:absolute;left:350px;top:780px;font:400 22px/28px "Saira Condensed",sans-serif}
  .origin{position:absolute;left:745px;top:816px;font:400 14px/1 "Saira Condensed",sans-serif}
  .steps{position:absolute;left:863px;top:155px;width:285px;height:176px;background:var(--panel-blue)}
  .steps-title{position:absolute;left:32px;top:-7px;background:var(--orange);font-size:11px;font-weight:600;padding:2px 6px;letter-spacing:-.2px}
  .step{position:absolute;width:90px;font-size:7px;line-height:9px}
  .step-icon{width:48px;height:48px;background:linear-gradient(135deg,#e6e6e6,#5c5c5c);border:1px solid var(--white);margin-bottom:4px}
  .steps-rule{position:absolute;left:16px;right:16px;top:91px;height:1px;background:var(--white)}
  p{margin:0}
  .gap{margin-top:14.5px}
</style>
</head>
<body>
<main class="label">
  <section class="col col-left">
    <p>Where To Use: Walls cabinets, cellings, trim and doors. Use over drywall, wood, concrete/brick plaster and wallpaper. See bellow for preparation steps:</p>
    <p>How Much You Need: For one coat coverage, apply at a maximum of 400 square feet per gallon. Rough or textured surfaces may require more allow for 125-300 square feet per gallon. Do not thin.</p>
    <p>What Tools To Use: May be applied with a quality roller, a nylon/polyester brush, or a paint pad How To Apply Room and surface temperature must be 50 degrees Fahrenheit. Allow at least 4 hours of drying time before recoating. Mix gallons togheter for color and sheen uniformity when using more than one gallon of the same product</p>
    <p>Care for Freshly Painted Surfaces. Freshly painted surfaced may be washed either 30 days- Until then avoid touching, wiping, or wetting the surface. Then clean with mild, non-abrasive, non-oily cleanser and water. Do not place objects on painted sirfaces untill throughly dry. Soap and Water Cleanup</p>
    <p>HOW TO PREPARE THE SURFACE</p>
    <p>Previously Painted Surfaces: Remove loose paint, Wash with a mild, non-abrasive, non-oily cleanser and water. Rinse completely, let dry Patch holes and cracks with speckling paste and let dry. Sand patched area and wipe off residue. Send all smooth or glossy surfaces, nnse well. Unpainted Surfaces: Wallboard or brywall Concrete/brick Allow new masonry to sure at least 30 days Etch smooth unpainted concrete. Remove all loose concrete and efflorescence: Rinse and allow to dry Plaster (new) Must be died and cured for 30 days. Prime with primer. Let dry 4 hours before top coating. Wallpaper Vinyl coated wallpaper may be coated if all seams and edges are glued tight, Self-sand and wipe clean. Use primer and alllow 24 hours to dry.</p>
  </section>

  <section class="ingredients">
    <h3><span>CAS NO.</span><span>INGREDIENTS</span></h3>
    <div class="ing-row"><span>7732-18-5..............................................</span><span>Water</span></div>
    <div class="ing-row"><span>Propietary..............................................</span><span>Vinyl Polymer</span></div>
    <div class="ing-row"><span>13463-67-7..............................................</span><span>Titanium Dioxide</span></div>
    <div class="ing-row"><span>Proprietary..............................................</span><span>Acrylic Polymer</span></div>
    <div class="ing-row"><span>471-34-1..............................................</span><span>Calcium Carbonate</span></div>
    <div class="ing-row"><span>14464-46-1..............................................</span><span>Cristobalite</span></div>
    <p class="ing-note">NON-PHOTOCHEMICALLY REACTIVE</p>
  </section>

  <div class="finish-tag">SEMI - GLOSS</div>
  <div class="brand"><span class="brand-mark"></span><span>Coat &amp; Gleam</span></div>
  <p class="tagline">Premium Paint at Outlet Prices</p>
  <p class="grade">Premium Grade</p>
  <p class="claim claim-1">EXCEPTIONAL DURABILITY</p>
  <div class="claim-rule"></div>
  <p class="claim claim-2">LUXURIOUS FINISH</p>
  <div class="art" role="img" aria-label="Paint roller over a grey brush stroke"></div>
  <p class="product">Latex Paint</p>
  <p class="use">INTERIOR / EXTERIOR</p>
  <div class="seal" role="img" aria-label="Freeze warning seal"></div>
  <p class="volume">1 Gal.<br>(124 OZ/3.667 Lts.)</p>
  <p class="origin">Made in the US.</p>

  <section class="col col-right" style="top:63px">
    <p class="orange" style="font-weight:600;font-size:11px">SOLID VINYL WALLPAPER CANNOT BE PAINTED</p>
    <p class="gap">CAUTIONS CONTAINS CRYSTALLINE SILICA- Use Cleanup: Clean tools, spills and splatters immediately with soap and water.</p>
  </section>

  <section class="steps">
    <span class="steps-title">KEEP FROM FREEZING-DO NOT THIN</span>
    <div class="step" style="left:17px;top:16px"><div class="step-icon" role="img" aria-label="Hand wiping surface icon"></div>Clean, dull and dry surface</div>
    <div class="step" style="left:118px;top:16px"><div class="step-icon" role="img" aria-label="Stirring paint icon"></div>Stir paint thoroughly</div>
    <div class="step" style="left:220px;top:16px"><div class="step-icon" role="img" aria-label="Brush at ceiling edge icon"></div>Start at ceiling edge</div>
    <div class="steps-rule"></div>
    <div class="step" style="left:17px;top:99px"><div class="step-icon" role="img" aria-label="Roller pattern icon"></div>Paint "N" pattern-fill in</div>
    <div class="step" style="left:118px;top:99px"><div class="step-icon" role="img" aria-label="Trim brush icon"></div>Paint trim last</div>
    <div class="step" style="left:220px;top:99px"><div class="step-icon" role="img" aria-label="Washing brush icon"></div>Soap and water clean up</div>
  </section>

  <section class="col col-right" style="top:339px">
    <p style="letter-spacing:1.3px">only with adecuate ventilation To avoid</p>
    <p style="text-align:justify">overexposure, open windows and doors or use other means to ensure fresh air entry during aplication and drying. If you experience eye watering, headaches, or dizzyness, increase fresh air, or wear respiratory protection or leave the area. Adecuate ventilation required when sending or abrading the dried film. If adequate ventilation cannot ve provided wear an approved particulate respirator. Follow resporator manufacturer's directions for respirator use. Avoid contact with eyes and skin Wash hands after using.</p>
    <p>Keep container<br>closed when not in use Do not transfer contents to other containers for storage</p>
    <p class="gap">FIRST AID. In case of eye contact flush thoroughly with large amounts of water. Get medical attention if mation persists, fallowed, call Poison Control Center. hospital emergency room, or physician immediately</p>
    <p class="gap">DELAYED EFFECTS FROM LONG TERM OVEREXPOSURE Abrading on sanding of the dry film may release crystalino silica which has been shown to cause lung damage and cancer under long term expusurur</p>
    <p class="gap">WARNING: This product contains chemicals known to the State of California to cause cancer and birth defects or other reproductive ha</p>
    <p class="gap orange">DO NOT TAKE INTERNALLY<br>KEEP OUT OF THE REACH OF CHILDREN</p>
  </section>
</main>
</body>
</html>
```